Business Card for brovaLINK

Create a Business Card with an existing logo for brovaLINK AG. We are a Information Technology company that does consulting and developing SW to automate business processes. The main colors are given from the logo.

Industry/Entity Type

Business

Requirements
Nice to have
• we use a a font style Century Gothic in our documents

```html
<!DOCTYPE html>
<html lang="en">
<head>
<meta charset="utf-8">
<title>brovaLINK Business Card</title>
<link href="https://fonts.googleapis.com/css2?family=Questrial&family=Montserrat:wght@700&display=swap" rel="stylesheet">
<style>
  :root {
    --bg: #e9ebee;
    --blue-deep: #1a4fb0;
    --blue-mid: #1e86d6;
    --blue-light: #27a8e6;
    --green: #8cc63f;
    --green-deep: #3cb54a;
    --white: #ffffff;
    --ink: #2f2f33;
  }
  * { margin: 0; padding: 0; box-sizing: border-box; }
  html, body { width: 1200px; height: 900px; overflow: hidden; }
  body {
    background: var(--bg);
    font-family: "Questrial", "Century Gothic", sans-serif;
    position: relative;
  }
  .card {
    position: absolute;
    left: 250px;
    width: 700px;
    height: 400px;
    overflow: hidden;
    box-shadow: 0 6px 18px rgba(0,0,0,0.18);
  }
  .card-back {
    top: 30px;
    background: radial-gradient(ellipse at 55% 45%, var(--blue-light) 0%, var(--blue-mid) 45%, var(--blue-deep) 100%);
  }
  .card-front { top: 470px; background: var(--white); }

  .brand {
    display: flex;
    align-items: center;
    gap: 14px;
    font-family: "Questrial", "Century Gothic", sans-serif;
    font-weight: 400;
    letter-spacing: 0.5px;
  }
  .brand-dot { border-radius: 50%; background: var(--green); flex: none; }

  .back-brand {
    position: absolute;
    left: 0; right: 0; top: 150px;
    justify-content: center;
    color: var(--white);
    font-size: 64px;
  }
  .back-brand .brand-dot { width: 44px; height: 44px; }
  .back-url {
    position: absolute;
    left: 0; right: 0; bottom: 40px;
    text-align: center;
    color: var(--white);
    font-size: 18px;
    letter-spacing: 1px;
  }

  .front-shape { position: absolute; inset: 0; }
  .front-brand {
    position: absolute;
    left: 58px; top: 160px;
    color: var(--ink);
    font-size: 52px;
  }
  .front-brand .brand-dot { width: 36px; height: 36px; }

  .contact {
    position: absolute;
    right: 40px; top: 50px;
    text-align: right;
    color: var(--white);
  }
  .contact-name {
    font-family: "Montserrat", "Century Gothic", sans-serif;
    font-weight: 700;
    font-size: 25px;
  }
  .contact-role { color: var(--green); font-size: 19px; margin-top: 2px; }
  .contact-lines { list-style: none; margin-top: 44px; font-size: 19px; line-height: 27px; }
  .contact-lines li { display: flex; justify-content: flex-end; align-items: center; gap: 8px; }
  .contact-lines svg { width: 16px; height: 16px; flex: none; }
  .contact-address { margin-top: 34px; font-size: 19px; line-height: 26px; padding-right: 24px; }
</style>
</head>
<body>

<section class="card card-back">
  <div class="brand back-brand"><span class="brand-dot"></span><span>brovaLINK</span></div>
  <div class="back-url">www.brovalink.ch</div>
</section>

<section class="card card-front">
  <svg class="front-shape" viewBox="0 0 700 400" preserveAspectRatio="none" aria-hidden="true">
    <defs>
      <linearGradient id="panelBlue" x1="0" y1="0" x2="1" y2="1">
        <stop offset="0" stop-color="#27a8e6"/>
        <stop offset="0.55" stop-color="#1e86d6"/>
        <stop offset="1" stop-color="#1a4fb0"/>
      </linearGradient>
      <linearGradient id="leftWash" x1="0" y1="0" x2="1" y2="0">
        <stop offset="0" stop-color="#f4f6fb"/>
        <stop offset="1" stop-color="#ffffff"/>
      </linearGradient>
    </defs>
    <rect width="700" height="400" fill="url(#leftWash)"/>
    <path d="M380 0 C 420 150, 330 330, 90 400 L 120 400 C 360 335, 440 160, 400 0 Z" fill="var(--green)"/>
    <path d="M400 0 C 440 160, 360 335, 120 400 L 700 400 L 700 0 Z" fill="url(#panelBlue)"/>
    <path d="M400 0 C 440 160, 360 335, 120 400" fill="none" stroke="#ffffff" stroke-width="5"/>
  </svg>

  <div class="brand front-brand"><span class="brand-dot"></span><span>brovaLINK</span></div>

  <div class="contact">
    <div class="contact-name">Lukas Brandt</div>
    <div class="contact-role">CEO</div>
    <ul class="contact-lines">
      <li>+41 56 210 48 37
        <svg viewBox="0 0 16 16"><circle cx="8" cy="8" r="8" fill="var(--green)"/><path d="M4 6 Q8 3 12 6 L11 8 L9 7 L7 7 L5 8 Z M5 9 H11 V12 H5 Z" fill="#fff"/></svg></li>
      <li>+41 79 604 25 19
        <svg viewBox="0 0 16 16"><circle cx="8" cy="8" r="8" fill="var(--green)"/><path d="M5 4 L7 4 L8 6 L7 7 Q8 9 9 10 L10 9 L12 10 L12 12 Q7 12 5 6 Z" fill="#fff"/></svg></li>
      <li>www.brovalink.ch
        <svg viewBox="0 0 16 16"><circle cx="8" cy="8" r="8" fill="var(--green)"/><circle cx="8" cy="8" r="4.5" fill="none" stroke="#fff" stroke-width="1.2"/><path d="M3.5 8 H12.5 M8 3.5 V12.5" stroke="#fff" stroke-width="1"/></svg></li>
      <li>lukas.brandt@brovalink.ch
        <svg viewBox="0 0 16 16"><circle cx="8" cy="8" r="8" fill="var(--green)"/><rect x="4" y="5" width="8" height="6" fill="#fff"/><path d="M4 5 L8 8.5 L12 5" fill="none" stroke="var(--green)" stroke-width="1"/></svg></li>
    </ul>
    <div class="contact-address">Lindenweg 12,<br>5430 Wettingen, Switzerland</div>
  </div>
</section>

</body>
</html>
```